Captivating packaging design for sports company.

We need a packaging design that encompasses our resistance bands workout set. Our focus is quality, convenience, and versatility. The design should be tailored to our broad array of customer across all paths. We would like the packaging to reflect our brand and product features such as: the LBS(weight) listed on each of the bands, convenience for travel and at home, highest quality, for all fitness levels, and free eBook. We'd also like to include a couple of our reviews on the packaging. Please refer to our listing on Varlo for additional information https://www.shopvarlo.com/Brisklane-Athletics-Resistance-Workout-Carrying/dp/K47TR2XMNQ/ref=sr_1_1?ie=UTF8&qid=1470453588&sr=8-1&keywords=brisklane+athletics+resistance+bands
Please reach out with additional questions for any further details. Thank you.
Target Market(s)
Sports, fitness, and health enthusiasts of all ages.
Industry/Entity Type
It Company
Look and feel
Each slider illustrates characteristics of the customer's brand and the style your logo design should communicate.

```html
<!DOCTYPE html>
<html lang="en">
<head>
<meta charset="utf-8">
<title>Brisklane Athletics Resistance Bands Packaging</title>
<link rel="stylesheet" href="https://fonts.googleapis.com/css2?family=Krona+One&display=swap">
<style>
  :root {
    --brand-green: #2eb08b;
    --deep-green: #1f8a6b;
    --ink: #0b0b0b;
    --paper: #ffffff;
    --backdrop: #d9d9d9;
    --band-light: #3fc79c;
    --band-dark: #17775b;
  }
  * { box-sizing: border-box; margin: 0; padding: 0; }
  html, body { width: 1200px; height: 1200px; overflow: hidden; }
  body {
    background: var(--backdrop);
    font-family: "Krona One", "Arial Black", sans-serif;
    position: relative;
  }
  .package { position: absolute; left: 120px; top: 220px; width: 960px; height: 760px; display: flex; }

  /* Side panel */
  .side-panel {
    width: 300px; height: 100%;
    background: var(--brand-green);
    color: var(--paper);
    position: relative;
  }
  .brand-lockup { display: flex; align-items: center; gap: 12px; }
  .brand-dot { width: 30px; height: 30px; border-radius: 50%; flex: none; }
  .brand-name { line-height: 1.15; text-transform: uppercase; }
  .side-panel .brand-lockup { position: absolute; left: 34px; top: 60px; }
  .side-panel .brand-dot { background: var(--paper); }
  .side-panel .brand-name { font-size: 17px; color: var(--paper); }

  .box-contents {
    position: absolute; left: 40px; top: 220px; width: 220px;
    font-size: 12px; line-height: 1.5; text-align: center; text-transform: uppercase;
    list-style: none;
  }
  .box-contents .contents-title { margin-bottom: 2px; }
  .slogan {
    position: absolute; left: 30px; top: 415px;
    font-size: 44px; line-height: 1.14; text-transform: uppercase;
  }
  .resistance-callout {
    position: absolute; left: 16px; right: 0; bottom: 0; height: 150px;
    background: var(--paper);
    color: var(--brand-green);
    display: flex; align-items: center; justify-content: center;
    text-align: center; font-size: 17px; line-height: 1.25; text-transform: uppercase;
    padding: 0 24px;
  }

  /* Front panel */
  .front-panel { width: 660px; height: 100%; background: var(--paper); position: relative; overflow: hidden; }
  .front-header {
    height: 330px; background: var(--ink); position: relative;
  }
  .front-header .brand-lockup { position: absolute; left: 40px; top: 130px; }
  .front-header .brand-dot { background: var(--brand-green); width: 40px; height: 40px; }
  .front-header .brand-name { font-size: 19px; color: var(--brand-green); }
  .headline {
    position: absolute; left: 310px; top: 88px; color: var(--paper); text-transform: uppercase;
  }
  .headline .kicker { display: block; font-size: 17px; margin-bottom: 8px; }
  .headline .title { display: block; font-size: 31px; line-height: 1.12; }

  .product-copy {
    position: absolute; left: 40px; top: 380px; width: 240px;
    font-size: 15px; line-height: 1.35; color: var(--ink);
  }
  .product-copy .set-name { margin-bottom: 24px; }
  .feature-list { list-style: none; }

  .band-photo {
    position: absolute; right: -20px; top: 350px; width: 320px; height: 360px;
    border-radius: 160px 0 0 160px;
    background: radial-gradient(circle at 55% 50%, var(--band-light), var(--band-dark) 75%, #e9f2ee 100%);
  }

  .bonus-badge {
    position: absolute; left: 330px; top: 560px; width: 240px; height: 240px;
    border-radius: 50%; border: 5px solid var(--brand-green); background: var(--paper);
    text-align: center; color: var(--brand-green);
  }
  .bonus-badge .bonus-title { display: block; margin-top: 28px; font-size: 24px; text-transform: uppercase; }
  .bonus-badge .bonus-text { display: block; font-size: 12px; line-height: 1.3; margin-top: 4px; }
  .ebook-cover {
    position: absolute; left: 82px; top: 120px; width: 76px; height: 100px;
    background: linear-gradient(160deg, #f2f2f2, #9aa3a0);
  }
</style>
</head>
<body>
  <div class="package">
    <section class="side-panel">
      <div class="brand-lockup">
        <span class="brand-dot"></span>
        <span class="brand-name">Brisklane<br>Athletics</span>
      </div>
      <ul class="box-contents">
        <li class="contents-title">In the box</li>
        <li>x1 Yellow - 2-4LB</li>
        <li>x1 Green - 4-6LB</li>
        <li>x1 Blue - 10-12LB</li>
        <li>x1 Red - 15-20LB</li>
        <li>x1 Black - 25-30LB</li>
        <li>Carry case</li>
        <li>E-book</li>
      </ul>
      <p class="slogan">Tone<br>Burn<br>Build</p>
      <p class="resistance-callout">Up to 75lbs<br>of total<br>resistance</p>
    </section>

    <section class="front-panel">
      <header class="front-header">
        <div class="brand-lockup">
          <span class="brand-dot"></span>
          <span class="brand-name">Brisklane<br>Athletics</span>
        </div>
        <h1 class="headline">
          <span class="kicker">High Quality</span>
          <span class="title">Resistance<br>Bands</span>
        </h1>
      </header>

      <div class="band-photo" role="img" aria-label="Photo of a green resistance band tube with a black strap and metal clip"></div>

      <div class="product-copy">
        <p class="set-name">Brisklane Athletics Resistance Band Workout Set</p>
        <ul class="feature-list">
          <li>4 Colourful Bands</li>
          <li>Door Anchor</li>
          <li>2 Handles</li>
          <li>2 Ankle Straps</li>
          <li>Carrying Case</li>
        </ul>
      </div>

      <div class="bonus-badge">
        <span class="bonus-title">Bonus</span>
        <span class="bonus-text">Product and<br>Workout<br>Guide eBook</span>
        <div class="ebook-cover" role="img" aria-label="Cover of the workout guide eBook"></div>
      </div>
    </section>
  </div>
</body>
</html>
```